Website Re-design and extension of an existing website

I have a Wordpress website currently and I need it to be upgraded. I have MOST of the content to get it started and the rest (video's, pictures ect) are on the way. I want to know if it is possible to convert my existing website into a Personal Brand website with a public speaking emphasis. I would like to have my website modeled after the following website:

http://www.vokalmira.com/

I have attached a document entitled "Website Outline & Content" that has all of the text on it and it has red headlines that indicate where something needs to be added or designed. I will be happy to give more detail if needed.

Things I still need to get to you in order to design the website;

-Demo video
-Full length public speaking video

Target Market(s)

Corporations, universities, trade associations, private events

Coding

Coded - Design and coding required

Requirements
Must have
• Pictures, links, downloadable forms, MULTIPLE video's embedded, my logo, keep the colors in sync with my existing marketing material
Nice to have
• I would like my design colors thematic as already inherent in my marketing materials (see my Speaker One Sheet)

```html
<!DOCTYPE html>
<html lang="en">
<head>
<meta charset="utf-8">
<title>Brock Dalton – Your Holistic Lifestyle Hacker</title>
<link href="https://fonts.googleapis.com/css2?family=Oswald:wght@400;500;600&family=Open+Sans:wght@400;600;700&display=swap" rel="stylesheet">
<style>
:root{
  --olive:#85834f;
  --olive-dark:#3b3a2a;
  --ink:#2a2a22;
  --cream:#f0ecdb;
  --paper:#f5f5f2;
  --text:#444;
  --muted:#777;
  --footer:#252522;
  --white:#fff;
  --red:#d9302c;
  --blue:#2b5aa6;
}
*{box-sizing:border-box;margin:0;padding:0}
html,body{width:1200px;height:4390px;overflow:hidden}
body{font-family:"Open Sans",Arial,sans-serif;color:var(--text);background:var(--white);position:relative}
h1,h2,h3,h4{font-family:"Oswald",Arial,sans-serif;font-weight:500;color:var(--ink)}
.section{position:absolute;left:0;width:1200px}
.abs{position:absolute}
.btn{display:inline-block;font-family:"Open Sans",Arial,sans-serif;font-weight:700;font-size:14px;text-align:center;border-radius:30px}
.photo{position:absolute}

/* header */
.site-header{top:0;height:112px;background:var(--white)}
.brand{left:100px;top:26px;display:flex;align-items:center;gap:12px}
.brand-dot{width:56px;height:56px;border-radius:50%;background:var(--olive-dark)}
.brand-name{font-family:"Oswald",sans-serif;font-size:32px;font-weight:600;color:var(--olive-dark);line-height:1}
.brand-tag{font-family:"Oswald",sans-serif;font-size:11px;color:var(--olive-dark);letter-spacing:1px;margin-top:4px}
.connect{right:100px;top:38px;display:flex;align-items:center;gap:8px;font-family:"Oswald",sans-serif;font-size:20px;color:var(--ink)}
.soc{width:34px;height:34px;border-radius:50%}
.main-nav{top:112px;height:48px;background:var(--olive-dark);display:flex;align-items:center;padding-left:92px}
.main-nav a{color:var(--white);font-size:13px;text-decoration:none;padding:0 14px;line-height:48px;font-weight:600}
.main-nav a.active{background:var(--olive)}

/* hero */
.hero{top:160px;height:520px;background:linear-gradient(90deg,#ece6cf,#f4f1e4 60%,#ebe6d2);overflow:hidden}
.hero-figure{left:140px;top:20px;width:220px;height:430px;background:linear-gradient(#cfc6ad,#8a8a78);border-radius:6px}
.hero-title{left:470px;top:128px;font-size:64px;color:var(--ink);letter-spacing:1px}
.hero-sub{left:472px;top:220px;font-size:18px;color:var(--ink)}
.hero-btn{left:472px;top:278px;width:518px;height:44px;line-height:44px;background:var(--olive);color:var(--white);font-size:17px}
.hero-wave{left:0;bottom:0}

/* intro */
.intro{top:680px;height:330px;text-align:center}
.intro h2{position:absolute;top:90px;width:100%;font-size:30px;font-weight:400}
.intro p{position:absolute;top:143px;width:100%;font-size:18px;color:var(--olive)}
.sheets{position:absolute;top:196px;left:0;width:100%;display:flex;justify-content:center;gap:14px}
.sheet{height:48px;line-height:48px;padding:0 26px;font-size:14px;border-radius:30px;font-weight:600;box-shadow:0 2px 8px rgba(0,0,0,.15);background:var(--white);color:var(--olive)}
.sheet.dark{background:var(--olive-dark);color:var(--white)}

/* problem */
.problem{top:1010px;height:555px;background:var(--paper)}
.problem h2{position:absolute;top:78px;width:100%;text-align:center;font-size:26px;font-weight:400}
.card{position:absolute;top:155px;width:237px;height:322px;background:var(--white);border:1px solid #ddd;text-align:center}
.card.featured{background:var(--olive-dark);border-color:var(--olive-dark)}
.card-icon{width:84px;height:84px;border-radius:50%;background:#efe9d6;margin:30px auto 0}
.card.featured .card-icon{background:var(--white)}
.card h3{font-family:"Open Sans",sans-serif;font-size:15px;font-weight:600;margin-top:14px;line-height:1.35}
.card.featured h3{color:var(--white)}
.card p{font-size:12px;color:var(--muted);padding:8px 24px 0;line-height:1.5}
.card.featured p{color:#ddd}
.card .btn{position:absolute;left:58px;bottom:34px;width:120px;height:36px;line-height:34px;border-radius:3px;border:1px solid #333;font-size:13px;background:var(--white);color:var(--ink)}

/* consent band */
.consent{top:1565px;height:340px;background:var(--olive);text-align:center;color:var(--white)}
.consent h2{position:absolute;top:70px;width:100%;font-size:25px;color:var(--white);font-weight:400}
.consent p{position:absolute;top:128px;left:200px;width:800px;font-size:13px;line-height:1.9}

/* about */
.about{top:1905px;height:420px}
.about h2{position:absolute;left:100px;top:70px;font-size:25px;font-weight:400}
.about p{position:absolute;left:100px;top:122px;width:560px;font-size:13px;line-height:2;color:var(--muted)}
.about .btn{position:absolute;left:100px;top:312px;width:130px;height:38px;line-height:38px;background:var(--olive-dark);color:var(--white);font-size:13px}
.about-video{left:685px;top:80px;width:415px;height:270px;background:linear-gradient(#6d6a64,#4a4536 55%,#6f6852)}
.play{left:877px;top:195px;width:52px;height:38px;border-radius:9px;background:var(--red)}

/* testimonials */
.testimonials{top:2325px;height:470px;background:linear-gradient(135deg,#f1f1ef,#e9e9e6)}
.testimonials h2{position:absolute;top:93px;width:100%;text-align:center;font-size:26px;font-weight:400}
.quote{position:absolute;top:165px;width:433px;height:222px;background:var(--white);box-shadow:0 2px 8px rgba(0,0,0,.08);padding:22px 24px}
.quote-avatar{width:66px;height:66px;border-radius:50%;background:#b9a996;float:left;margin-right:16px}
.quote h4{font-family:"Open Sans",sans-serif;font-size:13px;font-weight:700;margin-top:6px}
.quote .role{font-size:11px;color:var(--muted);margin-top:4px}
.quote .badge{position:absolute;right:24px;top:36px;width:108px;height:24px;line-height:24px;color:var(--white);font-size:11px;text-align:center;font-weight:700}
.quote p{clear:both;padding-top:18px;font-size:12px;line-height:1.7;color:var(--muted)}
.arrow-round{top:250px;width:40px;height:40px;border-radius:50%;border:2px solid #cfcfcf}

/* clients */
.clients{top:2795px;height:250px}
.client{position:absolute;top:86px;width:150px;height:76px;border:1px solid #ddd;background:var(--white);display:flex;align-items:center;justify-content:center;font-family:"Open Sans",sans-serif;font-weight:700;font-size:15px;color:var(--ink)}

/* join */
.join{top:3044px;height:186px;background:var(--olive-dark)}
.join h2{position:absolute;left:100px;top:44px;width:830px;white-space:nowrap;font-family:"Open Sans",sans-serif;font-size:16.5px;font-weight:700;color:var(--white)}
.join .btn{position:absolute;left:100px;top:95px;width:180px;height:46px;line-height:46px;background:var(--olive);color:var(--white);font-size:16px}
.book{left:950px;top:-24px;width:175px;height:220px;background:linear-gradient(#d8c8a0,#8c7a55);box-shadow:4px 4px 10px rgba(0,0,0,.4)}

/* press */
.press{top:3230px;height:575px}
.press h2{position:absolute;top:76px;width:100%;text-align:center;font-size:26px;font-weight:400}
.post{position:absolute;top:142px;width:237px;height:345px;border:1px solid #ddd;background:var(--white)}
.post-img{height:172px}
.post h4{font-family:"Open Sans",sans-serif;font-size:12px;font-weight:700;padding:22px 14px 0;line-height:1.5}
.post p{font-size:12px;color:var(--muted);padding:8px 14px 0;line-height:1.6}
.post .meta{position:absolute;bottom:16px;left:14px;font-size:11px;color:var(--ink)}

/* footer */
.footer{top:3805px;height:585px;background:var(--footer);color:var(--white)}
.footer h2{position:absolute;top:100px;width:100%;text-align:center;color:var(--white);font-size:32px;font-weight:400}
.footer h3{position:absolute;font-family:"Open Sans",sans-serif;color:var(--white);font-size:17px;font-weight:600}
.field{position:absolute;height:30px;background:var(--white);font-size:11px;color:#999;padding:7px 10px}
.submit{left:628px;top:410px;width:100px;height:32px;line-height:32px;background:var(--olive);color:var(--white);font-size:13px}
.info{position:absolute;left:784px;display:flex;align-items:center;gap:18px;font-size:12px;color:#ddd}
.info-ic{width:36px;height:36px;border-radius:50%;border:1px solid #777;display:flex;align-items:center;justify-content:center;flex:none}
.fsoc{position:absolute;top:410px;width:32px;height:32px;border-radius:50%}
.copyright{position:absolute;top:540px;width:100%;text-align:center;font-size:11px;color:#bbb}
.footer-rule{position:absolute;left:100px;top:505px;width:1000px;height:1px;background:#444}
</style>
</head>
<body>

<header class="section site-header">
  <div class="abs brand">
    <span class="brand-dot"></span>
    <div><div class="brand-name">BROCK DALTON</div><div class="brand-tag">YOUR HOLISTIC LIFESTYLE HACKER</div></div>
  </div>
  <div class="abs connect">CONNECTED WITH US :
    <span class="soc" style="background:#3b5998" role="img" aria-label="Social profile"></span>
    <span class="soc" style="background:#1da1f2" role="img" aria-label="Social profile"></span>
    <span class="soc" style="background:#e02a26" role="img" aria-label="Video channel"></span>
    <span class="soc" style="background:#0077b5" role="img" aria-label="Professional profile"></span>
  </div>
</header>

<nav class="section main-nav">
  <a class="active">Home</a><a>About Brock Dalton</a><a>Motivational Speaker/Keynote</a><a>Workshop Presenter</a><a>Author</a><a>Coaching</a><a>Blog</a><a>Online Courses</a><a>Contact Brock Dalton</a>
</nav>

<section class="section hero">
  <div class="photo hero-figure" role="img" aria-label="Portrait of the speaker standing in a grey t-shirt"></div>
  <h1 class="abs hero-title">BROCK DALTON</h1>
  <div class="abs hero-sub">Sugar Addiction Expert, Holistic Health Expert, Author &amp; Speaker</div>
  <div class="abs btn hero-btn">See How Brock Dalton Can Help You or Your Organization</div>
  <svg class="abs hero-wave" width="1200" height="90" viewBox="0 0 1200 90">
    <path d="M0 40 Q300 95 620 55 T1200 10 L1200 90 L0 90Z" fill="#3b3a2a"/>
    <path d="M0 58 Q300 110 620 72 T1200 32 L1200 90 L0 90Z" fill="#fff"/>
  </svg>
</section>

<section class="section intro">
  <h2>YOUR HOLISTIC LIFESTYLE HACKER</h2>
  <p>Lose Your Mind &amp; Find Your Health!</p>
  <div class="sheets">
    <span class="sheet dark">&#8681; Download Brock's Speaker One Sheet</span>
    <span class="sheet">&#8681; Download Brock's Media Sheet</span>
    <span class="sheet">&#8681; Download Brock's College Speaker One Sheet</span>
  </div>
</section>

<section class="section problem">
  <h2>SUGAR ADDICTION (THE STEALTH ADDICTION) IS DESTROYING</h2>
  <div class="card featured" style="left:100px"><div class="card-icon"></div><h3>Your bottom-line</h3><p>Sed ut perspiciatis unde omnis iste natus error sit voluptatem accusan tium doloremque laudantium</p><span class="btn">CLICK HERE</span></div>
  <div class="card" style="left:354px"><div class="card-icon"></div><h3>Your Insurance<br>Premiums</h3><p>Sed ut perspiciatis unde omnis iste natus error sit voluptatem accusan</p><span class="btn">CLICK HERE</span></div>
  <div class="card" style="left:609px"><div class="card-icon"></div><h3>The health of<br>your employees</h3><p>Sed ut perspiciatis unde omnis iste natus error sit voluptatem accusan</p><span class="btn">CLICK HERE</span></div>
  <div class="card" style="left:864px"><div class="card-icon"></div><h3>The culture<br>of your company</h3><p>Sed ut perspiciatis unde omnis iste natus error sit voluptatem accusan</p><span class="btn">CLICK HERE</span></div>
</section>

<section class="section consent">
  <h2>WITHOUT YOUR KNOWLEDGE OR CONSENT!</h2>
  <p>For over 17 years, Brock Dalton has tirelessly helped executives, employees, and everyday people achieve lasting health and fitness by helping them "lose their minds." Using his unique 4-quadrant coaching system, speaking platform, and online training courses, Brock has helped hundreds of people shed their limiting beliefs, eat better, drop sugar addiction and transform their bodies and minds. Brock delights in helping people see through the self-deception of being "normal" and invites his students to discover and accept the extraordinary people they truly are. If you are ready to transform physically, mentally, emotionally, and spiritually, it is time for you to meet Brock Dalton, your holistic lifestyle hacker!</p>
</section>

<section class="section about">
  <h2>ABOUT BROCK DALTON</h2>
  <p>Hello, my friend, my name is Brock Dalton, and I am so honored that you want to know more about me! It feels good to be loved, and please know that the love is reciprocated! I am not your typical fast-talking public speaker, coach, or teacher... nor am I a genius. If you were to put me in a room with 1000 random people and then measure all of our IQs, I would likely fall somewhere in the middle or slightly below average (what I hate it when that happens)! Speaking of the word "average", I want to share with you my relationship with this very unique concept.</p>
  <span class="btn">READ MORE</span>
  <div class="photo about-video" role="img" aria-label="Video still of the speaker outdoors at sunset by a mountain view"></div>
  <svg class="abs play" viewBox="0 0 52 38"><path d="M20 11 L34 19 L20 27Z" fill="#fff"/></svg>
</section>

<section class="section testimonials">
  <h2>CLIENT TESTIMONIALS</h2>
  <svg class="abs arrow-round" style="left:72px" viewBox="0 0 40 40"><path d="M23 12 L15 20 L23 28" stroke="#bbb" stroke-width="2" fill="none"/></svg>
  <svg class="abs arrow-round" style="left:1088px" viewBox="0 0 40 40"><path d="M17 12 L25 20 L17 28" stroke="#bbb" stroke-width="2" fill="none"/></svg>
  <div class="quote" style="left:152px">
    <div class="quote-avatar" role="img" aria-label="Reviewer portrait"></div>
    <h4>DANA WELLS RT</h4><div class="role">CLINICAL MANAGER</div>
    <span class="badge" style="background:var(--blue)">SOCIAL REVIEW</span>
    <p>Sed ut perspiciatis unde omnis iste natus error sit voluptatem accusantium doloremque laudantium, totam rem aperiam, eaque ipsa quae ab illo inventore veritatis et quasi architecto beatae vitae dicta sunt explicabo nemo enim ipsam voluptatem quia voluptas sit aspernatur aut odit aut fugit.</p>
  </div>
  <div class="quote" style="left:615px">
    <div class="quote-avatar" role="img" aria-label="Reviewer portrait"></div>
    <h4>CHIEF RADIATION THERAPIST,</h4><div class="role">RIVERSIDE CANCER CENTER</div>
    <span class="badge" style="background:var(--red)">SEARCH REVIEW</span>
    <p>Sed ut perspiciatis unde omnis iste natus error sit voluptatem accusantium doloremque laudantium, totam rem aperiam, eaque ipsa quae ab illo inventore veritatis et quasi architecto beatae vitae dicta sunt explicabo nemo enim ipsam voluptatem quia voluptas sit aspernatur aut odit aut fugit.</p>
  </div>
</section>

<section class="section clients">
  <svg class="abs" style="left:98px;top:112px" width="16" height="24"><path d="M12 2 L3 12 L12 22" stroke="#222" stroke-width="3" fill="none"/></svg>
  <div class="client" style="left:128px">Vantor</div>
  <div class="client" style="left:286px">Marlow Events</div>
  <div class="client" style="left:444px">Northgate Advisory</div>
  <div class="client" style="left:602px">Lumen Labs</div>
  <div class="client" style="left:760px">Marlow Events</div>
  <div class="client" style="left:918px">Northgate Advisory</div>
  <svg class="abs" style="left:1088px;top:112px" width="16" height="24"><path d="M4 2 L13 12 L4 22" stroke="#222" stroke-width="3" fill="none"/></svg>
</section>

<section class="section join">
  <h2>Become a Holistic Health Hacker and receive a FREE 30-Day Meal Plan crafted by Brock!</h2>
  <span class="btn">JOIN NOW !</span>
  <div class="photo book" role="img" aria-label="Book cover with a person holding their head"></div>
</section>

<section class="section press">
  <h2>PRESS RELEASES</h2>
  <div class="post" style="left:100px"><div class="post-img" style="background:linear-gradient(#d9a35a,#6d5a45)" role="img" aria-label="Speaker portrait at sunset"></div><h4>NEMO ENIM IPSAM VOLUPTATEM QUIA VOLUPTASPERNATUR</h4><p>Lorem ipsum dolor sit amet, consectetur adipiscing elit, sed do eiusmod tempor</p><div class="meta">&#9679; By Admin &nbsp; &#9633; November 2017</div></div>
  <div class="post" style="left:354px"><div class="post-img" style="background:linear-gradient(#a5a39a,#5d5a52)" role="img" aria-label="Speaker portrait outdoors"></div><h4>NEMO ENIM IPSAM VOLUPTATEM QUIA VOLUPTASPERNATUR</h4><p>Lorem ipsum dolor sit amet, consectetur adipiscing elit, sed do eiusmod tempor</p><div class="meta">&#9679; By Admin &nbsp; &#9633; November 2017</div></div>
  <div class="post" style="left:609px"><div class="post-img" style="background:linear-gradient(#9fb3c4,#5a6470)" role="img" aria-label="Speaker portrait under blue sky"></div><h4>NEMO ENIM IPSAM VOLUPTATEM QUIA VOLUPTASPERNATUR</h4><p>Lorem ipsum dolor sit amet, consectetur incididunt ut labore et dolore magna</p><div class="meta">&#9679; By Admin &nbsp; &#9633; November 2017</div></div>
  <div class="post" style="left:864px"><div class="post-img" style="background:linear-gradient(#c9c4b6,#7c7566)" role="img" aria-label="Speaker portrait in winter landscape"></div><h4>NEMO ENIM IPSAM VOLUPTATEM QUIA VOLUPTASPERNATUR</h4><p>Lorem ipsum dolor sit amet, consectetur adipiscing elit, sed do eiusmod tempor</p><div class="meta">&#9679; By Admin &nbsp; &#9633; November 2017</div></div>
</section>

<footer class="section footer">
  <svg class="abs" style="left:0;top:-40px" width="1200" height="80" viewBox="0 0 1200 80"><path d="M0 70 Q400 0 700 30 T1200 20 L1200 80 L0 80Z" fill="#252522"/></svg>
  <h2>CONTACT US</h2>
  <h3 style="left:100px;top:172px">Contact form</h3>
  <div class="field" style="left:100px;top:218px;width:312px">Name</div>
  <div class="field" style="left:418px;top:218px;width:310px">Phone no.</div>
  <div class="field" style="left:100px;top:260px;width:628px">Email</div>
  <div class="field" style="left:100px;top:302px;width:628px;height:80px">Message</div>
  <span class="abs btn submit">SUBMIT</span>
  <h3 style="left:784px;top:172px">Contact Information</h3>
  <div class="info" style="top:215px"><span class="info-ic"><svg width="14" height="18" viewBox="0 0 14 18"><path d="M7 1a6 6 0 0 0-6 6c0 4 6 10 6 10s6-6 6-10a6 6 0 0 0-6-6z" fill="#fff"/></svg></span><span>44 quis nostrud exercitation<br>near el aliqui</span></div>
  <div class="info" style="top:267px"><span class="info-ic"><svg width="16" height="16" viewBox="0 0 16 16"><path d="M3 1l3 3-2 2c1 2 3 4 5 5l2-2 3 3-2 3C6 15 1 10 1 3z" fill="#fff"/></svg></span><span>Phone : 555 014 2290</span></div>
  <div class="info" style="top:315px"><span class="info-ic"><svg width="16" height="12" viewBox="0 0 16 12"><rect x="1" y="1" width="14" height="10" fill="none" stroke="#fff"/><path d="M1 1l7 6 7-6" stroke="#fff" fill="none"/></svg></span><span>hello@brockdalton.com</span></div>
  <h3 style="left:784px;top:366px">Social Media</h3>
  <span class="fsoc" style="left:784px;background:#3b5998" role="img" aria-label="Social profile"></span>
  <span class="fsoc" style="left:824px;background:#1da1f2" role="img" aria-label="Social profile"></span>
  <span class="fsoc" style="left:864px;background:#0077b5" role="img" aria-label="Professional profile"></span>
  <span class="fsoc" style="left:904px;background:#e02a26" role="img" aria-label="Video channel"></span>
  <div class="footer-rule"></div>
  <div class="copyright">Copyright © 2017 Brock Dalton Coaching All rights reserved.</div>
</footer>

</body>
</html>
```